Workshop PPT Update for AI Transformation Sessions

Our strategic consulting firm runs strategy workshops using slides as workshop exercises. These slides are used to communicate to the participants in advance, run the workshops and produce the final deliverable.

It is time for a design "upgrade". We'd like them to be more engaging, hipper and more interesting. These slides are utilitarian, so clean and usable is good. I have attached the example of what we have today. I have also attached an example of another company's slides that I like.

We can't rip off their design nor can we go away 100% from what we have. But I think it is possible to "update" our look to something closer to their look. Grey colors are fine with some color pop.

Slide styles needed are - 1) Cover Page, 2) Instructions Page, 3) Bullet list 4) Worksheet (place for participants to add content 5) Table, 6) Two column.

```html
<!DOCTYPE html>
<html lang="en">
<head>
<meta charset="utf-8">
<title>BrightPath – AI Transformation Workshop Slides</title>
<link href="https://fonts.googleapis.com/css2?family=Lato:wght@400;700;900&family=Roboto:wght@400;500;700&display=swap" rel="stylesheet">
<style>
:root{
  --canvas:#8e8e8e;
  --slate:#474a5c;
  --slate-deep:#3c3f50;
  --red:#c23a3f;
  --red-soft:#d24a4f;
  --ink:#2b2b2b;
  --muted:#6f6f6f;
  --white:#ffffff;
  --row:#f3f3f3;
  --rule:#e2e2e2;
}
*{box-sizing:border-box;margin:0;padding:0}
html,body{width:1200px;height:3976px;overflow:hidden}
body{background:var(--canvas);font-family:"Roboto",Arial,sans-serif;color:var(--ink);position:relative}
.slide{position:absolute;left:85px;width:1030px;height:580px;background:var(--white);overflow:hidden}
.abs{position:absolute}
.brand{font-family:"Lato",Arial,sans-serif;font-weight:400;font-size:40px;letter-spacing:-.5px;color:var(--slate);line-height:1}
.brand.on-dark{color:var(--white)}
.side{position:absolute;left:0;top:0;width:313px;height:580px;background:var(--slate)}
.side-rule{position:absolute;left:319px;top:0;width:5px;height:580px;background:var(--slate)}
.side-heading{position:absolute;left:60px;font-family:"Lato",Arial,sans-serif;font-weight:700;color:var(--white);font-size:33px;line-height:39px}

/* slide 1 */
.s1 .photo-panel{position:absolute;left:0;top:0;width:445px;height:580px;background:var(--slate)}
.s1 .photo{position:absolute;left:58px;top:73px;width:440px;height:440px;border-radius:50%;border:5px solid var(--red);box-shadow:0 0 0 6px var(--white) inset;background:radial-gradient(circle at 45% 40%,#d9dbe0,#a9acb4 55%,#6d7180)}
.checklist{position:absolute;left:540px;top:127px;list-style:none}
.checklist li{display:flex;align-items:center;height:84px;font-size:22px;color:var(--ink)}
.checklist svg{margin-right:18px;flex:none}

/* slide 2 */
.meta{position:absolute;left:60px;font-size:23px;color:var(--white)}
.meta b{font-weight:500;color:var(--red-soft);display:inline-block}
.prep{position:absolute;left:62px;top:370px;list-style:none;color:var(--white);font-size:21px;line-height:39px}
.steps{position:absolute;left:351px;top:20px}
.step{position:absolute;left:0;width:650px;height:64px;display:flex;align-items:center}
.icon-dot{width:64px;height:64px;border-radius:50%;background:var(--red);flex:none;display:flex;align-items:center;justify-content:center}
.step-text{margin-left:28px}
.step-text h3,.principle h3{font-size:15px;font-weight:700;color:var(--ink);margin-bottom:6px}
.step-text p,.principle p{font-size:15px;color:var(--muted);line-height:22px}
.deliver{position:absolute;left:437px;top:546px;font-size:15px;font-weight:700}
.deliver span{margin-right:30px}

/* slide 3 */
.s3{background:var(--slate)}
.s3 .backdrop{position:absolute;inset:0;background:radial-gradient(ellipse at 55% 60%,#5a5d6e,#474a5c 55%,#3c3f50)}
.cover{position:absolute;left:0;width:100%;text-align:center;color:var(--white)}
.cover-title{font-family:"Lato",Arial,sans-serif;font-weight:900;font-size:66px;top:262px}
.cover-sub{font-family:"Lato",Arial,sans-serif;font-size:33px;top:363px}

/* slide 4 */
.slide-title{font-family:"Lato",Arial,sans-serif;font-weight:700;font-size:33px;color:var(--slate-deep)}
.plan{position:absolute;left:62px;top:91px;width:906px;border-collapse:collapse;font-size:12px;color:#444;box-shadow:0 3px 10px rgba(0,0,0,.12)}
.plan th{background:var(--red);color:var(--white);font-weight:700;font-size:15px;height:56px;text-align:center}
.plan td{height:99px;text-align:center;border-right:1px solid var(--rule);line-height:20px}
.plan tr.alt td{background:var(--row)}
.plan td.merged{background:var(--white)!important}

/* slide 5 */
.side-item{position:absolute;left:59px;color:var(--white);line-height:20px;font-size:14px}
.side-item.head{font-family:"Lato",Arial,sans-serif;font-weight:700;font-size:21px;line-height:26px}
.guide-line{position:absolute;left:421px;width:580px;font-size:16px;line-height:20px}
.guide-line.lbl{font-weight:500}
.guide-line.red{color:var(--red);font-weight:500}
.guide-line.step-h{font-weight:700}
.guide-line.small{font-size:13px;color:#444}

/* slide 6 */
.principle{position:absolute;left:351px;width:650px;display:flex;align-items:center}
.principle .icon-dot{margin-right:28px}
.side-q{position:absolute;left:59px;top:224px;font-size:21px;line-height:39px;color:var(--white)}
</style>
</head>
<body>

<!-- Slide 1: instructions -->
<section class="slide s1" style="top:93px">
  <div class="photo-panel"></div>
  <div class="photo" role="img" aria-label="Photo of two businessmen reviewing work at a laptop"></div>
  <div class="abs brand" style="left:753px;top:26px">BrightPath</div>
  <ul class="checklist">
    <li><svg width="20" height="20" viewBox="0 0 20 20"><circle cx="10" cy="10" r="8" fill="none" stroke="#c23a3f" stroke-width="2.5"/><path d="M6 10.2l2.8 2.7L14 7.6" fill="none" stroke="#c23a3f" stroke-width="2.5"/></svg>Complete the Engagement Sizing Survey.</li>
    <li><svg width="20" height="20" viewBox="0 0 20 20"><circle cx="10" cy="10" r="8" fill="none" stroke="#c23a3f" stroke-width="2.5"/><path d="M6 10.2l2.8 2.7L14 7.6" fill="none" stroke="#c23a3f" stroke-width="2.5"/></svg>Collect relevant inputs.</li>
    <li><svg width="20" height="20" viewBox="0 0 20 20"><circle cx="10" cy="10" r="8" fill="none" stroke="#c23a3f" stroke-width="2.5"/><path d="M6 10.2l2.8 2.7L14 7.6" fill="none" stroke="#c23a3f" stroke-width="2.5"/></svg>Determine workshop participants &amp; date.</li>
    <li><svg width="20" height="20" viewBox="0 0 20 20"><circle cx="10" cy="10" r="8" fill="none" stroke="#c23a3f" stroke-width="2.5"/><path d="M6 10.2l2.8 2.7L14 7.6" fill="none" stroke="#c23a3f" stroke-width="2.5"/></svg>Send invites, to include pre-work</li>
  </ul>
</section>

<!-- Slide 2: workshop overview -->
<section class="slide s2" style="top:735px">
  <div class="side"></div>
  <div class="side-rule"></div>
  <div class="abs brand on-dark" style="left:60px;top:26px">BrightPath</div>
  <h2 class="side-heading" style="top:124px">Workshop<br>Overview</h2>
  <div class="meta" style="top:220px"><b style="width:145px">Participants:</b>Execs</div>
  <div class="meta" style="top:272px"><b style="width:148px">Duration:</b>2 hrs.</div>
  <div class="meta" style="top:322px"><b>Prep Work:</b></div>
  <ul class="prep">
    <li>Org Strategy</li><li>2023 Goal Performance</li><li>Existing policies</li><li>Pre-thinking questions</li>
  </ul>
  <div class="steps">
    <div class="step" style="top:0"><div class="icon-dot"><svg width="32" height="32" viewBox="0 0 32 32" fill="none" stroke="#fff" stroke-width="2"><rect x="5" y="6" width="14" height="18"/><path d="M9 11h6M9 15h6M9 19h4"/><circle cx="24" cy="20" r="3"/><path d="M19 28c0-3 2-5 5-5s5 2 5 5"/></svg></div><div class="step-text"><h3>Confirm Company Direction</h3><p>Recap organizational purpose, values, vision &amp; winning strategy.</p></div></div>
    <div class="step" style="top:89px"><div class="icon-dot"><svg width="32" height="32" viewBox="0 0 32 32" fill="none" stroke="#fff" stroke-width="2"><circle cx="16" cy="16" r="5"/><circle cx="16" cy="16" r="10"/><path d="M16 2v4M16 26v4M2 16h4M26 16h4"/></svg></div><div class="step-text"><h3>Develop AI Vision</h3></div></div>
    <div class="step" style="top:177px"><div class="icon-dot"><svg width="32" height="32" viewBox="0 0 32 32" fill="none" stroke="#fff" stroke-width="2"><rect x="4" y="6" width="24" height="16"/><path d="M12 27h8M16 22v5M9 12h14M9 16h9"/></svg></div><div class="step-text"><h3>Develop AI Guiding Principles</h3><p>Developed AI Guiding Principles, supporting policies to include approved tools</p></div></div>
    <div class="step" style="top:265px"><div class="icon-dot"><svg width="32" height="32" viewBox="0 0 32 32" fill="none" stroke="#fff" stroke-width="2"><circle cx="16" cy="17" r="6"/><path d="M16 3v5M4 17h4M24 17h4M16 25v4M13 5l3-3 3 3"/></svg></div><div class="step-text"><h3>Agree on a Governance Approach</h3><p>Agreed upon governance approach, structure, &amp; executive champion.</p></div></div>
    <div class="step" style="top:353px"><div class="icon-dot"><svg width="32" height="32" viewBox="0 0 32 32" fill="none" stroke="#fff" stroke-width="2"><rect x="4" y="4" width="24" height="12"/><circle cx="8" cy="22" r="2"/><circle cx="16" cy="22" r="2"/><circle cx="24" cy="22" r="2"/><path d="M5 29h6M13 29h6M21 29h6"/></svg></div><div class="step-text"><h3>Agree on a Training &amp; Learning Approach</h3><p>Set approach to training &amp; continuous learning.</p></div></div>
    <div class="step" style="top:441px"><div class="icon-dot"><svg width="32" height="32" viewBox="0 0 32 32" fill="none" stroke="#fff" stroke-width="2"><circle cx="10" cy="16" r="4"/><circle cx="22" cy="16" r="4"/><path d="M3 28c0-4 3-6 7-6s7 2 7 6M15 28c0-4 3-6 7-6s7 2 7 6"/><rect x="12" y="3" width="12" height="7"/></svg></div><div class="step-text"><h3>Determine Rollout &amp; Communication</h3><p>Organizational rollout &amp; continuous communication</p></div></div>
  </div>
  <div class="deliver"><span>Deliverables</span><span>Your Company’s AI Playbook</span></div>
</section>

<!-- Slide 3: cover -->
<section class="slide s3" style="top:1377px">
  <div class="backdrop" role="img" aria-label="Faint photo of chess pieces on a board joined by network lines"></div>
  <div class="cover" style="top:180px"><span class="brand on-dark" style="font-size:46px">BrightPath</span></div>
  <div class="cover cover-title">Kickoff &amp; Discovery</div>
  <div class="cover cover-sub">Sizing &amp; Scoping AI Transformation</div>
</section>

<!-- Slide 4: table -->
<section class="slide s4" style="top:2020px">
  <div class="abs brand" style="left:62px;top:18px">BrightPath</div>
  <div class="abs slide-title" style="left:760px;top:18px">Plan Structure</div>
  <table class="plan">
    <colgroup><col style="width:82px"><col style="width:88px"><col style="width:273px"><col style="width:224px"><col style="width:239px"></colgroup>
    <thead><tr><th colspan="2">Level</th><th>Planning Element &amp; Definition</th><th>Accountability/Owner</th><th>Frequency of Modification</th></tr></thead>
    <tbody>
      <tr><td>1</td><td>What<br><br>(overall)</td><td>Strategic Priorities</td><td>N/A</td><td>3+ years</td></tr>
      <tr class="alt"><td>1.1</td><td>What<br><br>(this year)</td><td>Goals<br>Outcomes &amp; Strategies</td><td>Executive Leadership</td><td>1-3 years</td></tr>
      <tr><td>1.1.1</td><td rowspan="2" class="merged">How</td><td>Key Performance Indicators<br>and/or Initiatives</td><td></td><td>1 year<br>(w/ qrtly targets)</td></tr>
      <tr class="alt"><td>1.1.1.1</td><td>Action Items</td><td></td><td>Quarterly/Monthly</td></tr>
    </tbody>
  </table>
</section>

<!-- Slide 5: two column worksheet -->
<section class="slide s5" style="top:2662px">
  <div class="side"></div>
  <div class="side-rule"></div>
  <div class="abs brand on-dark" style="left:60px;top:26px">BrightPath</div>
  <p class="side-item head" style="top:151px">Your Existing Material</p>
  <p class="side-item" style="top:195px">Company Values</p>
  <p class="side-item" style="top:229px">Current Policies (GDPR, CCPA, etc.)</p>
  <p class="side-item" style="top:263px">Legal Guidance</p>
  <p class="side-item" style="top:299px">OTHER</p>
  <p class="side-item head" style="top:339px">Examples for Inspiration</p>
  <p class="side-item" style="top:384px">See next slides</p>
  <p class="side-item head" style="top:432px">ThinkBot Prompts</p>
  <p class="side-item" style="top:475px">HERE</p>
  <div class="abs slide-title" style="left:421px;top:28px">Creating your AI Guiding Principles</div>
  <p class="guide-line lbl" style="top:140px">Purpose:</p>
  <p class="guide-line" style="top:178px">To create behavioral statements that everyone is expected to adhere to.</p>
  <p class="guide-line red" style="top:212px">Instructions:</p>
  <p class="guide-line step-h" style="top:245px">Create the Outline</p>
  <p class="guide-line small" style="top:273px">Determine the topics that need a principle</p>
  <p class="guide-line step-h" style="top:308px">Audit the Outline.</p>
  <p class="guide-line small" style="top:336px">Look at the current policies to determine if all topics are covered.</p>
  <p class="guide-line step-h" style="top:379px">Draft the Guiding Principles.</p>
  <p class="guide-line step-h" style="top:419px">Determine which GPs need detailed policies.</p>
  <p class="guide-line step-h" style="top:461px">Determine which AI Tools support the GPs.</p>
  <p class="guide-line step-h" style="top:503px">Finalize via a legal and executive review.</p>
</section>

<!-- Slide 6: bullet list -->
<section class="slide s6" style="top:3304px">
  <div class="side"></div>
  <div class="side-rule"></div>
  <div class="abs brand on-dark" style="left:60px;top:26px">BrightPath</div>
  <h2 class="side-heading" style="left:59px;top:126px">AI Guiding<br>Principles</h2>
  <p class="side-q">What guides our<br>decision-making and<br>approach?</p>
  <div class="principle" style="top:27px"><div class="icon-dot"><svg width="36" height="36" viewBox="0 0 36 36" fill="none" stroke="#fff" stroke-width="2.5"><circle cx="18" cy="18" r="14"/><path d="M11 18l5 5 10-11"/></svg></div><div><h3>Principle #1</h3><p>Complete perspective from Executives, Directors, Managers &amp; Staff.<br>Conduct competitive analysis and customer research (optional).</p></div></div>
  <div class="principle" style="top:138px"><div class="icon-dot"><svg width="36" height="36" viewBox="0 0 36 36" fill="none" stroke="#fff" stroke-width="2.5"><circle cx="18" cy="18" r="14"/><path d="M11 18l5 5 10-11"/></svg></div><div><h3>Principle #2</h3><p>Complete perspective from Executives, Directors, Managers &amp; Staff.<br>Conduct competitive analysis and customer research (optional).</p></div></div>
  <div class="principle" style="top:248px"><div class="icon-dot"><svg width="36" height="36" viewBox="0 0 36 36" fill="none" stroke="#fff" stroke-width="2.5"><circle cx="18" cy="18" r="14"/><path d="M11 18l5 5 10-11"/></svg></div><div><h3>Principle #3</h3><p>Complete perspective from Executives, Directors, Managers &amp; Staff.<br>Conduct competitive analysis and customer research (optional).</p></div></div>
  <div class="principle" style="top:359px"><div class="icon-dot"><svg width="36" height="36" viewBox="0 0 36 36" fill="none" stroke="#fff" stroke-width="2.5"><circle cx="18" cy="18" r="14"/><path d="M11 18l5 5 10-11"/></svg></div><div><h3>Principle #4</h3><p>Complete perspective from Executives, Directors, Managers &amp; Staff.<br>Conduct competitive analysis and customer research (optional).</p></div></div>
  <div class="principle" style="top:470px"><div class="icon-dot"><svg width="36" height="36" viewBox="0 0 36 36" fill="none" stroke="#fff" stroke-width="2.5"><circle cx="18" cy="18" r="14"/><path d="M11 18l5 5 10-11"/></svg></div><div><h3>Principle #5</h3><p>Complete perspective from Executives, Directors, Managers &amp; Staff.<br>Conduct competitive analysis and customer research (optional).</p></div></div>
</section>

</body>
</html>
```